New Innovative Counselling and psychotherapy Service needs Business Card design

Keep it simple and professional. On one side, just company name and logo (perhaps in all blue) and maybe a tag line.

On other side (all white) my name and Qualifications in centre

Industry/Entity Type

Health And Wellness

Contact Information for Business Card

Dara Whelby
Counsellor & Psychotherapist
BSc (Psychol.), BA, Dip. (Couns. & Psych.), PG.Cert (CBT), FGTrK, ONRE

I will also require Mobile no, Email and web site address of which I'll pass on to final designer.

Font styles to use
Sans Serif

Requirements
Must have
• My Logo Only and please use the colours in logo that is in it.
Should not have
• Any other images

```html
<!DOCTYPE html>
<html lang="en">
<head>
<meta charset="utf-8">
<title>Thrive Lane – Business Card</title>
<link rel="stylesheet" href="https://fonts.googleapis.com/css2?family=Montserrat:wght@300;400;500&family=Nunito+Sans:ital,wght@0,400;0,900;1,400&display=swap">
<style>
  :root {
    --sky: #4cafe3;
    --sky-deep: #2f8fc8;
    --sky-pale: #e6f3fb;
    --leaf: #8cc152;
    --ink: #333638;
    --ink-soft: #4a4d50;
    --paper: #ffffff;
    --backdrop: #eeeae4;
    --rule: #c9c9c9;
  }
  * { box-sizing: border-box; margin: 0; padding: 0; }
  html, body { width: 1200px; height: 960px; overflow: hidden; }
  body {
    background: var(--backdrop);
    font-family: "Nunito Sans", sans-serif;
    color: var(--ink);
    position: relative;
  }
  .card {
    position: absolute;
    left: 250px;
    width: 700px;
    height: 400px;
    overflow: hidden;
    box-shadow: 0 6px 20px rgba(0,0,0,0.12);
  }

  /* Brand side */
  .card--brand { top: 50px; background: var(--sky); }
  .card--brand .brand {
    position: absolute;
    left: 150px; top: 160px;
    display: flex; align-items: center; gap: 26px;
  }
  .card--brand .brand-dot {
    width: 76px; height: 76px; border-radius: 50%;
    background: var(--paper);
  }
  .card--brand .brand-name {
    font-family: "Montserrat", sans-serif;
    font-weight: 300;
    font-size: 52px;
    letter-spacing: 1px;
    color: var(--paper);
  }
  .card--brand .web {
    position: absolute; left: 0; right: 0; bottom: 58px;
    text-align: center;
    font-family: "Montserrat", sans-serif;
    font-size: 15px; letter-spacing: 2px;
    color: var(--paper);
  }

  /* Contact side */
  .card--contact { top: 510px; background: var(--paper); }
  .decor-ring {
    position: absolute; right: 70px; top: 150px;
    width: 260px; height: 260px; border-radius: 50%;
    background: var(--sky-pale); opacity: 0.8;
  }
  .person { position: absolute; left: 70px; top: 52px; }
  .person-name {
    font-weight: 900; font-size: 30px; color: var(--ink);
    letter-spacing: 0.5px;
  }
  .person-role, .person-quals {
    font-size: 15px; line-height: 23px; color: var(--ink-soft);
  }
  .person-role { margin-top: 6px; }
  .divider {
    width: 72px; height: 1px; background: var(--rule);
    margin: 18px 0 22px;
  }
  .contact-list { list-style: none; }
  .contact-list li {
    display: flex; align-items: center; gap: 12px;
    font-family: "Montserrat", sans-serif;
    font-size: 18px; color: var(--ink); line-height: 30px;
  }
  .contact-list svg { width: 18px; height: 18px; }
  .card--contact .brand {
    position: absolute; right: 60px; top: 58px;
    display: flex; align-items: center; gap: 16px;
  }
  .card--contact .brand-dot {
    width: 46px; height: 46px; border-radius: 50%;
    background: var(--sky);
  }
  .card--contact .brand-name {
    font-family: "Montserrat", sans-serif;
    font-weight: 400; font-size: 28px; color: var(--ink-soft);
  }
  .waves { position: absolute; left: 0; bottom: 0; width: 700px; height: 400px; }
  .card--contact .web {
    position: absolute; right: 60px; bottom: 26px;
    font-family: "Montserrat", sans-serif;
    font-weight: 500; font-size: 21px; letter-spacing: 1.5px;
    color: var(--paper);
  }
</style>
</head>
<body>

<section class="card card--brand" aria-label="Card front">
  <div class="brand">
    <span class="brand-dot"></span>
    <span class="brand-name">Thrive Lane</span>
  </div>
  <p class="web">www.thrivelane.com</p>
</section>

<section class="card card--contact" aria-label="Card back">
  <div class="decor-ring"></div>

  <svg class="waves" viewBox="0 0 700 400" preserveAspectRatio="none" aria-hidden="true">
    <path d="M0 322 C150 345 300 352 440 338 C340 360 150 365 0 360 Z" fill="var(--leaf)"/>
    <path d="M0 360 C150 365 340 360 440 338 C540 318 640 330 700 360 L700 400 L0 400 Z" fill="var(--paper)"/>
    <path d="M170 372 C330 360 470 318 560 318 C620 318 670 335 700 352 L700 400 L200 400 Z" fill="var(--sky)"/>
    <path d="M300 378 C420 350 500 330 560 328 C500 345 420 368 360 400 L300 400 Z" fill="var(--sky-deep)" opacity="0.55"/>
  </svg>

  <div class="person">
    <h1 class="person-name">Dara Whelby</h1>
    <p class="person-role">Counsellor &amp; Psychotherapist</p>
    <p class="person-quals">BSc (Psychol.)<br>BA, Dip. (Couns. &amp; Psych.)<br>PG.Cert (CBT), FGTrK, ONRE</p>
    <div class="divider"></div>
    <ul class="contact-list">
      <li>
        <svg viewBox="0 0 24 24" aria-hidden="true"><path d="M6.6 10.8a15 15 0 0 0 6.6 6.6l2.2-2.2c.3-.3.7-.4 1-.2 1.1.4 2.3.6 3.6.6.6 0 1 .4 1 1V20c0 .6-.4 1-1 1A17 17 0 0 1 3 4c0-.6.4-1 1-1h3.5c.6 0 1 .4 1 1 0 1.3.2 2.5.6 3.6.1.3 0 .7-.2 1z" fill="var(--sky)"/></svg>
        000 000 0000
      </li>
      <li>
        <svg viewBox="0 0 24 24" aria-hidden="true"><rect x="2.5" y="5" width="19" height="14" fill="none" stroke="var(--sky)" stroke-width="1.6"/><path d="M2.5 5l9.5 8 9.5-8" fill="none" stroke="var(--sky)" stroke-width="1.6"/></svg>
        dara@thrivelane.com
      </li>
    </ul>
  </div>

  <div class="brand">
    <span class="brand-dot"></span>
    <span class="brand-name">Thrive Lane</span>
  </div>

  <p class="web">thrivelane.com</p>
</section>

</body>
</html>
```